Business card for wedding & event planning company

I'm looking for a well designed double sided business card to represent my wedding and event planning company.

It should include the fact we manage the following events:
Weddings, birthdays, conferences, product launches, fashion shows & conventions
in the following areas:
Wiltshire, Oxfordshire, Berkshire & London

My contact details to be included are:

Moira Stanwick
07514 283640
moira@bluefernevents.co.uk
www.bluefernevents.co.uk

My logo can be found at the following Filebarn location:
AI file: https://www.filebarn.example/s/k3mxpw8rt51bn7d/logo_sourcefile.ai
PNG file:
https://www.filebarn.example/s/h6qvlz2ncy90tue/logo_image.png

Target Market(s)

women aged 30-55

Industry/Entity Type

Wedding

Contact Information for Business Card

in the following areas:

Moira Stanwick
Event Planner
07514 283640

Font styles to use
Serif
Sans Serif
Script

Requirements
Must have
• Purple and white colour scheme
Should not have
• Black background
• Please don't submit any of the see-through business card designs.

```html
<!DOCTYPE html>
<html lang="en">
<head>
<meta charset="utf-8">
<title>Blue Fern Events – Business Card</title>
<link rel="stylesheet" href="https://fonts.googleapis.com/css2?family=Cinzel:wght@400;600&family=Crimson+Text:wght@400;600&display=swap">
<style>
  :root {
    --purple: #8b3097;
    --purple-deep: #7c2789;
    --purple-pattern: #82298f;
    --white: #ffffff;
    --stage: #ece8ee;
    --divider: #c9a6d0;
  }
  html, body {
    margin: 0;
    padding: 0;
    width: 1200px;
    height: 1000px;
    overflow: hidden;
    background: var(--stage);
  }
  .canvas {
    position: relative;
    width: 1200px;
    height: 1000px;
  }
  .card {
    position: absolute;
    left: 265px;
    width: 667px;
    height: 398px;
    border-radius: 24px;
    overflow: hidden;
    box-shadow: 0 4px 14px rgba(60, 30, 70, 0.18);
  }
  .card-front { top: 73px; background: var(--white); }
  .card-back  { top: 532px; background: var(--purple); }

  .brand {
    position: absolute;
    left: 0;
    width: 100%;
    text-align: center;
  }
  .brand-mark {
    display: block;
    margin: 0 auto;
  }
  .brand-name {
    display: block;
    font-family: "Crimson Text", serif;
    font-weight: 400;
    letter-spacing: 1px;
    line-height: 1;
  }
  .card-front .brand { top: 28px; }
  .card-front .brand-name { font-size: 46px; color: var(--purple-deep); margin-top: 8px; }
  .card-back .brand { top: 70px; }
  .card-back .brand-name { font-size: 56px; color: var(--white); margin-top: 10px; }

  .contact-band {
    position: absolute;
    top: 235px;
    left: 0;
    width: 100%;
    height: 104px;
    background: var(--purple);
    color: var(--white);
  }
  .person-name {
    position: absolute;
    right: 360px;
    top: 40px;
    font-family: "Cinzel", serif;
    font-size: 20px;
    letter-spacing: 0.5px;
    margin: 0;
    white-space: nowrap;
  }
  .band-divider {
    position: absolute;
    left: 332px;
    top: 26px;
    width: 1px;
    height: 48px;
    background: var(--divider);
  }
  .contact-list {
    position: absolute;
    left: 360px;
    top: 22px;
    margin: 0;
    padding: 0;
    list-style: none;
    font-family: "Crimson Text", serif;
    font-size: 17px;
    line-height: 20px;
  }
  .contact-list li { display: flex; align-items: center; gap: 6px; }
  .contact-list svg { width: 11px; height: 11px; flex: none; }

  .service-areas {
    position: absolute;
    top: 351px;
    width: 100%;
    text-align: center;
    margin: 0;
    font-family: "Crimson Text", serif;
    font-size: 17px;
    color: var(--purple-deep);
  }

  .back-pattern {
    position: absolute;
    inset: 0;
    background: radial-gradient(ellipse at center, var(--purple) 0%, var(--purple-pattern) 100%);
  }
  .event-types {
    position: absolute;
    top: 338px;
    width: 100%;
    text-align: center;
    margin: 0;
    font-family: "Crimson Text", serif;
    font-size: 17px;
    color: var(--white);
    letter-spacing: 0.2px;
  }
</style>
</head>
<body>
<main class="canvas">

  <section class="card card-front">
    <div class="brand">
      <svg class="brand-mark" width="96" height="96" viewBox="0 0 96 96" aria-hidden="true">
        <circle cx="48" cy="48" r="44" fill="none" stroke="var(--purple-deep)" stroke-width="1.5"/>
      </svg>
      <span class="brand-name">Blue Fern Events</span>
    </div>

    <div class="contact-band">
      <p class="person-name">Moira Stanwick</p>
      <span class="band-divider"></span>
      <ul class="contact-list">
        <li>
          <svg viewBox="0 0 12 12"><path d="M3 1 L5 3.5 L4 5 Q5 7 7 8 L8.5 7 L11 9 L9.5 11 Q5 11 2 7 Q0.5 4 1 2.5 Z" fill="var(--white)"/></svg>
          07514 283640
        </li>
        <li>
          <svg viewBox="0 0 12 12"><rect x="0.5" y="2" width="11" height="8" fill="var(--white)"/><path d="M0.5 2 L6 6.5 L11.5 2" fill="none" stroke="var(--purple)" stroke-width="1"/></svg>
          moira@bluefernevents.co.uk
        </li>
        <li>
          <svg viewBox="0 0 12 12"><circle cx="6" cy="6" r="5.2" fill="none" stroke="var(--white)" stroke-width="1"/><ellipse cx="6" cy="6" rx="2.2" ry="5.2" fill="none" stroke="var(--white)" stroke-width="0.9"/><line x1="0.8" y1="6" x2="11.2" y2="6" stroke="var(--white)" stroke-width="0.9"/></svg>
          www.bluefernevents.co.uk
        </li>
      </ul>
    </div>

    <p class="service-areas">Wiltshire, Oxfordshire, Berkshire &amp; London</p>
  </section>

  <section class="card card-back">
    <div class="back-pattern" role="img" aria-label="Repeating faint bird pattern in deep purple tones"></div>
    <div class="brand">
      <svg class="brand-mark" width="120" height="120" viewBox="0 0 120 120" aria-hidden="true">
        <circle cx="60" cy="60" r="55" fill="none" stroke="var(--white)" stroke-width="1.6"/>
      </svg>
      <span class="brand-name">Blue Fern Events</span>
    </div>
    <p class="event-types">Weddings, birthdays, Conferences, Product launches, Fashion shows &amp; Conventions</p>
  </section>

</main>
</body>
</html>
```